Quendle Pools & Patio Homepage Design

I am looking for someone to design a one-page website for a company called Quendle Pools & Patio. While the content will be different, the design should be similar to https://quendle-example.com/pools-patio/.
Industry/Entity Type
Pool Cleaning Service
Number of Pages Required
1 page
Font styles to use
Other font styles liked:
- See brand guidelines

Requirements
Must have
- Must be similar in style https://quendle-example.com/pools-patio/. Look at the Word Doc for the content.

```html
<!DOCTYPE html>
<html lang="en">
<head>
<meta charset="utf-8">
<title>Quendle Pools &amp; Patio</title>
<link href="https://fonts.googleapis.com/css2?family=Barlow+Condensed:wght@500;600;700&family=Kreon:wght@400;600;700&display=swap" rel="stylesheet">
<style>
:root{
  --navy:#0b4a7e;
  --navy-deep:#0a3f6e;
  --green:#2fd86a;
  --sky:#3b9fe2;
  --ink:#0a2a2a;
  --text:#2c3440;
  --white:#fff;
  --water-a:#1a78c4;
  --water-b:#0f5a9a;
}
*{margin:0;padding:0;box-sizing:border-box}
html,body{width:1200px;height:4389px;overflow:hidden}
body{position:relative;font-family:"Kreon",serif;color:var(--text);background:var(--white)}
.abs{position:absolute}
.head{font-family:"Barlow Condensed",sans-serif;font-weight:700;text-transform:uppercase;letter-spacing:.5px}
.btn{position:absolute;background:var(--green);color:var(--white);font-family:"Barlow Condensed",sans-serif;font-weight:700;font-size:20px;text-transform:uppercase;display:flex;align-items:center;justify-content:center}

/* top bar */
.topbar{left:0;top:0;width:1200px;height:120px;background:var(--white)}
.brand{display:flex;align-items:center;gap:12px;font-family:"Kreon",serif;font-weight:600;font-size:52px;color:var(--green)}
.brand-mark{width:44px;height:44px;background:var(--green);border-radius:6px}
.contact-chip{display:flex;align-items:center;gap:12px}
.chip-icon{width:36px;height:36px;border-radius:50%;background:var(--green);display:flex;align-items:center;justify-content:center}
.chip-label{font-size:17px;font-weight:700;color:var(--green)}
.chip-value{font-size:22px;color:var(--navy);font-weight:600;letter-spacing:.5px}
.chip-value.small{font-size:18px;font-weight:400}

/* nav */
.nav{left:0;top:120px;width:1200px;height:62px;background:var(--ink)}
.nav ul{list-style:none;display:flex;gap:43px;position:absolute;left:75px;top:18px}
.nav li{font-family:"Barlow Condensed",sans-serif;font-weight:700;font-size:21px;color:var(--white);text-transform:uppercase}
.nav li.active{color:var(--sky)}
.nav .signin{left:855px;top:0;width:118px;height:62px;background:var(--sky);color:var(--white);font-weight:700;font-size:17px;display:flex;align-items:center;justify-content:center;text-transform:uppercase;letter-spacing:1px}
.nav .quote{left:973px;top:0;width:153px;height:62px;background:var(--green);color:var(--white);font-weight:700;font-size:17px;display:flex;align-items:center;justify-content:center;text-transform:uppercase;letter-spacing:1px}

/* hero */
.hero{left:0;top:182px;width:1200px;height:708px;background:linear-gradient(160deg,#5c6a68 0%,#3e7f8f 35%,#2f8aa0 60%,#4a90a0 100%)}
.hero-title{left:75px;top:195px;font-size:70px;line-height:70px;color:var(--white)}
.dots{left:75px;top:634px;display:flex;gap:10px}
.dots span{width:11px;height:11px;border-radius:50%;background:var(--white)}
.dots span.on{background:var(--ink)}

/* quick contact */
.qc{width:510px;height:477px;background:rgba(11,74,126,.82);border-radius:8px;padding:30px}
.qc.solid{background:var(--navy)}
.qc h3{font-size:50px;color:var(--white);line-height:50px;margin-bottom:18px}
.qc .row{display:flex;gap:15px;margin-bottom:14px}
.field{flex:1;height:55px;background:var(--white);font-size:15px;color:#444;padding:0 15px;display:flex;align-items:center}
.qc .pref{font-size:18px;color:var(--white);margin:22px 0 8px}
.radios{display:flex;gap:22px;font-size:15px;color:var(--white)}
.radios span{display:flex;align-items:center;gap:8px}
.radios i{width:13px;height:13px;border-radius:50%;background:var(--white);display:inline-block}
.submit{margin-top:18px;height:55px;background:var(--sky);color:var(--white);font-family:"Barlow Condensed",sans-serif;font-weight:700;font-size:21px;display:flex;align-items:center;justify-content:center}

/* overview */
.sec-title{font-size:48px;color:var(--navy);line-height:48px}
.body-copy{font-size:15.5px;line-height:28px;color:var(--text)}

/* services */
.services{left:0;top:1587px;width:1200px;height:658px;background:linear-gradient(120deg,#2c7fbf 0%,#1c8fd4 40%,#1670b4 70%,#2a8ed0 100%)}
.services-deck{left:0;top:0;width:260px;height:658px;background:linear-gradient(180deg,#3b4d5e,#566574)}
.svc{width:330px;height:385px}
.svc-text{position:absolute;left:30px;right:30px;top:148px;text-align:center}
.svc-text h4{font-family:"Barlow Condensed",sans-serif;font-weight:700;font-size:28px;color:var(--green);text-transform:uppercase;margin-bottom:8px}
.svc-text p{font-size:15px;line-height:26px;color:var(--white)}

/* service area */
.area{left:0;top:2920px;width:1200px;height:343px;background:linear-gradient(180deg,#2b86c8 0%,#1d7bc0 50%,#1a6fb2 100%)}

/* footer */
.footer{left:0;top:3960px;width:1200px;height:429px;background:linear-gradient(135deg,#1c7cc4,#1a74bb 50%,#2384c9)}
.foot-h{font-family:"Barlow Condensed",sans-serif;font-weight:700;font-size:26px;color:var(--green);text-transform:uppercase}
.foot-list{list-style:none;font-size:16px;color:var(--white);line-height:30.5px}
.foot-small{font-size:15px;color:var(--white);line-height:23px}
.socials{display:flex;gap:22px}
.socials span{width:24px;height:24px;background:var(--white);border-radius:4px}
</style>
</head>
<body>

<!-- top bar -->
<header class="abs topbar">
  <div class="abs brand" style="left:75px;top:30px"><span class="brand-mark"></span>quendle</div>
  <div class="abs contact-chip" style="left:595px;top:36px">
    <span class="chip-icon"><svg width="18" height="18" viewBox="0 0 24 24"><path fill="#fff" d="M6.6 10.8a15.1 15.1 0 0 0 6.6 6.6l2.2-2.2a1 1 0 0 1 1-.25 11.4 11.4 0 0 0 3.6.57 1 1 0 0 1 1 1V20a1 1 0 0 1-1 1A17 17 0 0 1 3 4a1 1 0 0 1 1-1h3.5a1 1 0 0 1 1 1c0 1.25.2 2.45.57 3.57a1 1 0 0 1-.25 1z"/></svg></span>
    <div><div class="chip-label">Phone:</div><div class="chip-value">555-014-2290</div></div>
  </div>
  <div class="abs contact-chip" style="left:850px;top:36px">
    <span class="chip-icon"><svg width="18" height="18" viewBox="0 0 24 24"><path fill="#fff" d="M3 6h18v12H3z"/><path d="M3 6l9 7 9-7" stroke="#2fd86a" stroke-width="2" fill="none"/></svg></span>
    <div><div class="chip-label">Email:</div><div class="chip-value small">hello@quendle-example.com</div></div>
  </div>
</header>

<!-- nav -->
<nav class="abs nav">
  <ul>
    <li class="active">Home</li><li>About</li><li>Services</li><li>Learn</li><li>Locations</li><li>FAQs</li>
  </ul>
  <div class="abs signin">Sign In</div>
  <div class="abs quote">Get a Quote</div>
</nav>

<!-- hero -->
<section class="abs hero" role="img" aria-label="Pool cleaning equipment and hose beside sparkling pool water">
  <h1 class="abs head hero-title">Keep Your<br>Pool Sparkling<br>With Quendle!</h1>
  <div class="btn" style="left:75px;top:440px;width:178px;height:60px">Contact Us</div>
  <div class="abs dots" style="top:634px"><span class="on"></span><span></span><span></span><span></span></div>
  <form class="abs qc" style="left:616px;top:116px">
    <h3 class="head">Quick Contact</h3>
    <div class="row"><div class="field">First Name</div><div class="field">Last Name</div></div>
    <div class="row"><div class="field">Address</div><div class="field">Phone</div></div>
    <div class="row"><div class="field">Email Address</div></div>
    <div class="pref">Preferred Contact Method</div>
    <div class="radios"><span><i></i>Call</span><span><i></i>Text</span><span><i></i>Email</span></div>
    <div class="submit">SUBMIT</div>
  </form>
</section>

<!-- company overview -->
<section>
  <h2 class="abs head sec-title" style="left:75px;top:978px">Company Overview</h2>
  <div class="abs body-copy" style="left:75px;top:1040px;width:540px">
    <p>We’re Quendle Pools &amp; Patio, and we specialize in pool cleaning and repair services that will keep your pool looking its best. Our reliable and professional team is committed to helping you get the most out of your backyard oasis, ensuring it’s always ready for all types of fun when you want it. Our weekly pool cleaning service is affordable and ensures that your pool is properly taken care of throughout the swimming season.</p>
    <p style="margin-top:22px">When you choose us as your go-to for all things pools, relaxing days spent on a clean lounge chair are worry-free because we take care of all the hard work! From chemical balancing to scrubbing and filter maintenance - there’s nothing too big or small for us. So don’t wait any longer - trust Quendle to keep your pool sparkling all summer!</p>
  </div>
  <div class="btn" style="left:75px;top:1438px;width:178px;height:61px">Read More</div>
  <svg class="abs" style="left:665px;top:975px" width="480" height="530" viewBox="0 0 480 530">
    <defs><linearGradient id="ovg" x1="0" y1="0" x2="0" y2="1"><stop offset="0" stop-color="#cfe1ee"/><stop offset=".5" stop-color="#8a7a68"/><stop offset="1" stop-color="#3f8fb8"/></linearGradient></defs>
    <polygon points="250,2 478,110 468,410 228,528 4,398 20,100" fill="#2fd86a"/>
    <polygon points="238,4 470,134 470,396 238,526 8,396 8,134" fill="#fff"/>
    <polygon points="238,14 461,139 461,391 238,516 17,391 17,139" fill="url(#ovg)" role="img" aria-label="Technician cleaning a backyard pool beside a covered patio"/>
  </svg>
</section>

<!-- services -->
<section class="abs services" role="img" aria-label="Overhead view of a blue pool with cleaning hose and technician at the deck">
  <div class="abs services-deck"></div>
  <h2 class="abs head" style="left:0;width:1200px;text-align:center;top:90px;font-size:46px;color:var(--white)">Our Services</h2>
  <div class="abs svc" style="left:73px;top:183px">
    <svg width="330" height="385" class="abs"><polygon points="165,0 330,95 330,290 165,385 0,290 0,95" fill="#3b9fe2"/></svg>
    <div class="svc-text"><h4>Pool Cleaning</h4><p>Our weekly service includes chemical balancing, debris removal, wall and step scrubbing, and filter maintenance. Standard chemicals are included in the quoted price.</p></div>
  </div>
  <div class="abs svc" style="left:436px;top:183px">
    <svg width="330" height="385" class="abs"><polygon points="165,0 330,95 330,290 165,385 0,290 0,95" fill="#0a2a2a"/></svg>
    <div class="svc-text"><h4>Pool Maintenance</h4><p>We perform regular checks on all your pool equipment to make sure it runs efficiently and safely.</p></div>
  </div>
  <div class="abs svc" style="left:797px;top:183px">
    <svg width="330" height="385" class="abs"><polygon points="165,0 330,95 330,290 165,385 0,290 0,95" fill="#0b4a7e"/></svg>
    <div class="svc-text"><h4>Pool Repair</h4><p>From plumbing to equipment malfunctions, our qualified technicians can diagnose and repair any pool problem you may have.</p></div>
  </div>
</section>

<!-- technician -->
<section>
  <svg class="abs" style="left:55px;top:2325px" width="480" height="525" viewBox="0 0 480 525">
    <polygon points="260,2 478,125 470,420 240,523 8,420 4,120" fill="#2fd86a"/>
    <polygon points="240,4 462,131 462,393 240,520 18,393 18,131" fill="#fff"/>
    <polygon points="240,14 453,136 453,388 240,510 27,388 27,136" fill="#b9bcbf" role="img" aria-label="Portrait of the pool technician"/>
  </svg>
  <h2 class="abs head sec-title" style="left:616px;top:2418px">Meet Your Technician</h2>
  <div class="abs" style="left:616px;top:2490px;font-size:28px;font-weight:700;color:var(--sky)">Dale Merrow</div>
  <p class="abs body-copy" style="left:616px;top:2536px;width:500px;font-size:16.5px">"I understand that keeping your pool clean and well-maintained is a priority for you, which is why I'm committed to providing top-notch pool cleaning and repair services. Let's get started!"</p>
  <div class="btn" style="left:616px;top:2693px;width:178px;height:61px">Read More</div>
</section>

<!-- service area -->
<section class="abs area" role="img" aria-label="Resort pool with lounge chairs under a blue tint">
  <h2 class="abs head" style="left:0;width:1200px;text-align:center;top:98px;font-size:48px;color:var(--white)">Service Area</h2>
  <p class="abs" style="left:0;width:1200px;text-align:center;top:156px;font-size:29px;line-height:40px;color:var(--white);letter-spacing:.5px">Currently, we offer services in the Texas cities of Argyle,<br>Corinth, Flower Mound, and Lewisville.</p>
</section>

<!-- contact -->
<section>
  <h2 class="abs head sec-title" style="left:75px;top:3408px">Contact Us</h2>
  <p class="abs body-copy" style="left:75px;top:3470px;width:530px">Contact us today at Quendle Pools &amp; Patio, and let’s discuss how our professionals can help bridge the gap between what your pool could be and what it actually is! Get ready to have a worry-free experience with quality service delivered right on time so you can start enjoying those waves anytime soon!</p>
  <div class="abs head" style="left:75px;top:3638px;font-size:28px;color:var(--sky)">Give us a call today at <span style="color:var(--navy)">555-014-2290</span></div>
  <div class="btn" style="left:75px;top:3703px;width:178px;height:61px">Contact Us</div>
  <form class="abs qc solid" style="left:616px;top:3350px">
    <h3 class="head">Quick Contact</h3>
    <div class="row"><div class="field">First Name</div><div class="field">Last Name</div></div>
    <div class="row"><div class="field">Address</div><div class="field">Phone</div></div>
    <div class="row"><div class="field">Email Address</div></div>
    <div class="pref">Preferred Contact Method</div>
    <div class="radios"><span><i></i>Call</span><span><i></i>Text</span><span><i></i>Email</span></div>
    <div class="submit">SUBMIT</div>
  </form>
</section>

<!-- footer -->
<footer class="abs footer" role="img" aria-label="Pool water texture with a floating ring">
  <div class="abs brand" style="left:75px;top:58px;font-size:46px;color:var(--white)"><span class="brand-mark" style="background:var(--white);width:40px;height:40px"></span>quendle</div>
  <div class="abs foot-small" style="left:75px;top:140px;font-size:14px;line-height:22px">Copyright © 2023 Quendle-example.com<br>All Rights Reserved</div>
  <div class="abs foot-h" style="left:75px;top:240px">Follow Us</div>
  <div class="abs socials" style="left:75px;top:290px"><span></span><span></span><span></span><span></span><span style="width:30px"></span></div>

  <div class="abs foot-h" style="left:377px;top:70px">Site Map</div>
  <ul class="abs foot-list" style="left:377px;top:112px"><li>Home</li><li>About</li><li>Services</li><li>Learn</li><li>Locations</li><li>FAQs</li><li>Contact Us</li></ul>

  <div class="abs foot-h" style="left:585px;top:70px">Services</div>
  <ul class="abs foot-list" style="left:585px;top:112px;line-height:36px"><li>Pool Cleaning</li><li>Pool Maintenance</li><li>Pool Repair</li></ul>

  <div class="abs foot-h" style="left:832px;top:70px">Address</div>
  <div class="abs foot-small" style="left:832px;top:116px;font-weight:700;letter-spacing:.5px">QUENDLE POOLS &amp; PATIO</div>
  <div class="abs foot-small" style="left:832px;top:153px;color:var(--green);font-weight:700">Mailing Address:</div>
  <div class="abs foot-small" style="left:832px;top:178px;width:300px;line-height:28px">118 Harbor Lane, Suite 40,<br>Lakeview, TX 75000</div>
  <div class="abs foot-small" style="left:832px;top:248px;color:var(--green);font-weight:700">Phone:</div>
  <div class="abs foot-small" style="left:832px;top:273px">555-014-2290</div>
  <div class="abs foot-small" style="left:832px;top:310px;color:var(--green);font-weight:700">Email:</div>
  <div class="abs foot-small" style="left:832px;top:335px">hello@quendle-example.com</div>
</footer>

</body>
</html>
```